Young, dynamic furniture company needs a new business card design

We require a new business card design for our modern furniture company which supplies furniture and appliances to the property and development market.
Oakridge Interiors has become one of the leading furniture & appliance suppliers to the property market withing London. With over 10 years experience, we have increased our business to supply not only private landlords and managing agents, but also property developers, housing associations and local councils.
We offer not only a complete range of furniture which includes beds, wardrobes, dining sets and sofas, but also a high quality, full delivery and assembly service to help you with all our furnishing needs.

Target Market(s)

Private landlords, estate agents, letting agents, property management companies

Industry/Entity Type

Business

Contact Information for Business Card

Name,
Title,
Address,
Mobile,
Telephone,
Fax, Website, email address

Font styles to use
Sans Serif

Colors
3176b5
0555a3
85abd2
cfdeed

Requirements
Must have
• All the above information for each of our staff, along with our logo

```html
<!DOCTYPE html>
<html lang="en">
<head>
<meta charset="utf-8">
<title>Oakridge Interiors – Business Card</title>
<link rel="stylesheet" href="https://fonts.googleapis.com/css2?family=Roboto+Condensed:wght@400;700&family=Roboto:wght@400;500&display=swap">
<style>
  :root {
    --navy: #173f8c;
    --brand-blue: #0555a3;
    --mid-blue: #3176b5;
    --light-blue: #85abd2;
    --pale-blue: #cfdeed;
    --ink: #2b2b2b;
    --charcoal: #222326;
    --paper: #ffffff;
    --backdrop: #e9ebef;
  }
  * { box-sizing: border-box; margin: 0; padding: 0; }
  html, body { width: 1200px; height: 950px; overflow: hidden; }
  body {
    background: var(--backdrop);
    font-family: "Roboto Condensed", "Arial Narrow", sans-serif;
    position: relative;
  }
  .card {
    position: absolute;
    left: 250px;
    width: 700px;
    height: 400px;
    overflow: hidden;
    box-shadow: 0 6px 18px rgba(0,0,0,0.18);
  }

  /* Reverse side */
  .card-back {
    top: 45px;
    background: var(--navy);
    color: var(--paper);
    text-align: center;
  }
  .card-back .brand {
    position: absolute;
    top: 150px;
    left: 0; right: 0;
  }
  .brand-name {
    font-weight: 400;
    font-size: 32px;
    letter-spacing: 0.5px;
    line-height: 1;
    display: inline-flex;
    align-items: center;
    gap: 12px;
  }
  .brand-mark {
    width: 22px; height: 22px;
    background: currentColor;
    display: inline-block;
  }
  .brand-tagline {
    font-size: 12px;
    letter-spacing: 1px;
    text-transform: uppercase;
    margin-top: 6px;
  }
  .card-back .service {
    position: absolute;
    top: 268px;
    left: 0; right: 0;
    font-family: "Roboto", Arial, sans-serif;
    font-size: 17px;
    line-height: 1.5;
  }

  /* Front side */
  .card-front {
    top: 500px;
    background: var(--paper);
  }
  .card-front .shapes { position: absolute; inset: 0; }
  .card-front .brand {
    position: absolute;
    top: 120px;
    left: 95px;
    color: var(--ink);
  }
  .card-front .brand-tagline { color: var(--ink); margin-left: 34px; }
  .person {
    position: absolute;
    top: 250px;
    left: 215px;
    text-align: center;
  }
  .person-name {
    font-weight: 700;
    font-size: 24px;
    color: var(--navy);
    letter-spacing: 0.5px;
  }
  .person-title {
    font-size: 17px;
    color: var(--mid-blue);
    margin-top: 2px;
    letter-spacing: 0.5px;
  }
  .contact {
    position: absolute;
    top: 120px;
    right: 28px;
    list-style: none;
    color: var(--paper);
    font-family: "Roboto", Arial, sans-serif;
    font-size: 17px;
    text-align: right;
    line-height: 1.45;
  }
  .contact li { display: flex; justify-content: flex-end; align-items: center; gap: 8px; }
  .contact .address-line { margin-bottom: 0; }
  .contact .spacer { height: 10px; }
  .contact svg { width: 16px; height: 16px; fill: var(--paper); flex: none; }
</style>
</head>
<body>

<section class="card card-back" aria-label="Card reverse">
  <div class="brand">
    <div class="brand-name"><span class="brand-mark"></span>OAKRIDGE INTERIORS</div>
    <div class="brand-tagline">Trade Furniture Solutions</div>
  </div>
  <p class="service">High quality, full delivery &amp; assembly<br>service to help you with all our furnishing needs.</p>
</section>

<section class="card card-front" aria-label="Card front">
  <svg class="shapes" width="700" height="400" viewBox="0 0 700 400" aria-hidden="true">
    <defs>
      <linearGradient id="panelFill" x1="0" y1="0" x2="1" y2="1">
        <stop offset="0" stop-color="#3d86c8"/>
        <stop offset="1" stop-color="#0555a3"/>
      </linearGradient>
    </defs>
    <polygon points="0,352 520,352 500,400 0,400" fill="#222326"/>
    <polygon points="440,115 700,40 700,400 470,400" fill="url(#panelFill)"/>
  </svg>

  <div class="brand">
    <div class="brand-name"><span class="brand-mark"></span>OAKRIDGE INTERIORS</div>
    <div class="brand-tagline">Trade Furniture Solutions</div>
  </div>

  <div class="person">
    <div class="person-name">MARCUS HALE</div>
    <div class="person-title">PRESIDENT</div>
  </div>

  <ul class="contact">
    <li class="address-line">4127 Larchmont Avenue</li>
    <li class="address-line">Glen Cove, NY 11542</li>
    <li class="spacer"></li>
    <li>512 6390 4178
      <svg viewBox="0 0 16 16"><path d="M3 1h3l1.5 4-2 1.3a9 9 0 0 0 4.2 4.2L11 8.5l4 1.5v3a2 2 0 0 1-2 2A12 12 0 0 1 1 3a2 2 0 0 1 2-2z"/></svg>
    </li>
    <li>734 2061 8845
      <svg viewBox="0 0 16 16"><path d="M4.5 0h7A1.5 1.5 0 0 1 13 1.5v13a1.5 1.5 0 0 1-1.5 1.5h-7A1.5 1.5 0 0 1 3 14.5v-13A1.5 1.5 0 0 1 4.5 0zM5 2v10h6V2zm3 11a1 1 0 1 0 0 2 1 1 0 0 0 0-2z"/></svg>
    </li>
    <li>629 4857 1302
      <svg viewBox="0 0 16 16"><path d="M4 1h6l2 2v3h2a1 1 0 0 1 1 1v6a1 1 0 0 1-1 1H2a1 1 0 0 1-1-1V7a1 1 0 0 1 1-1h2zm1 1v4h6V3.5L9.5 2zM4 9v2h8V9z"/></svg>
    </li>
    <li>marcus@oakridge.com
      <svg viewBox="0 0 16 16"><path d="M1 3h14v10H1zm1.2 1L8 8.5 13.8 4zM2 5.2V12h12V5.2L8 9.8z"/></svg>
    </li>
  </ul>
</section>

</body>
</html>
```